Vantro cards

I am in the auto motive, transportation business I would like a business card that is Something cool, modern edgy, having to do with car culture. I offer towing service for high and exotic cars. I also provide towing for collisions and car accidents. I offer open and enclosed transport nationwide.

Target Market(s)

Car culture people high end auto collectors

Industry/Entity Type

Towing car carrier

Contact Information for Business Card

My company colors black yellow and silver

Font styles to use
Serif

```html
<!DOCTYPE html>
<html lang="en">
<head>
<meta charset="utf-8">
<title>Vantro Business Cards</title>
<link rel="stylesheet" href="https://fonts.googleapis.com/css2?family=Montserrat:wght@400;500;600&display=swap">
<style>
  :root {
    --bg: #d9d9d9;
    --card-white: #ffffff;
    --card-white-shade: #efefef;
    --black: #0a0a0a;
    --black-soft: #1c1c1c;
    --yellow: #f2c12e;
    --silver: #c9c9c9;
    --ink: #1a1a1a;
  }
  * { box-sizing: border-box; margin: 0; padding: 0; }
  html, body { width: 1200px; height: 1200px; overflow: hidden; }
  body {
    background: var(--bg);
    font-family: "Montserrat", sans-serif;
    position: relative;
  }
  .card {
    position: absolute;
    left: 170px;
    width: 860px;
    height: 492px;
    border-radius: 28px;
    overflow: hidden;
    box-shadow: 0 14px 30px rgba(0,0,0,0.25);
  }
  .card-front {
    top: 70px;
    background: linear-gradient(180deg, var(--card-white) 0%, var(--card-white-shade) 100%);
  }
  .card-back {
    top: 630px;
    background: var(--black);
  }

  /* front */
  .brand-mark {
    position: absolute;
    top: 92px;
    right: 70px;
    display: flex;
    align-items: center;
    gap: 14px;
  }
  .brand-square {
    width: 34px; height: 34px;
    background: var(--yellow);
  }
  .brand-name {
    font-size: 56px;
    font-weight: 600;
    color: var(--ink);
    letter-spacing: 2px;
    text-transform: uppercase;
  }
  .identity {
    position: absolute;
    left: 80px;
    top: 200px;
    padding-left: 24px;
    border-left: 6px solid var(--yellow);
  }
  .person-name {
    font-size: 46px;
    font-weight: 500;
    color: var(--yellow);
    line-height: 1;
    letter-spacing: 0.5px;
  }
  .person-role {
    font-size: 18px;
    font-weight: 500;
    color: var(--ink);
    margin-top: 6px;
    letter-spacing: 1px;
  }
  .contact-list {
    position: absolute;
    left: 110px;
    top: 310px;
    list-style: none;
  }
  .contact-item {
    display: flex;
    align-items: center;
    gap: 18px;
    font-size: 24px;
    color: var(--ink);
    height: 42px;
  }
  .contact-icon { width: 26px; height: 26px; flex: none; }
  .band-yellow {
    position: absolute;
    left: 0; bottom: 0;
    width: 560px; height: 34px;
    background: var(--yellow);
  }
  .band-black {
    position: absolute;
    right: 0; bottom: 0;
    width: 290px; height: 34px;
    background: var(--black);
  }

  /* back */
  .back-burst {
    position: absolute;
    inset: 0;
    background: radial-gradient(circle at 50% 50%, var(--black-soft) 0%, var(--black) 70%);
  }
  .back-brand {
    position: absolute;
    inset: 0;
    display: flex;
    align-items: center;
    justify-content: center;
    gap: 22px;
  }
  .back-square {
    width: 54px; height: 54px;
    background: var(--yellow);
  }
  .back-name {
    font-size: 92px;
    font-weight: 600;
    color: var(--yellow);
    letter-spacing: 4px;
    text-transform: uppercase;
  }
</style>
</head>
<body>

<section class="card card-front">
  <div class="brand-mark">
    <span class="brand-square"></span>
    <span class="brand-name">Vantro</span>
  </div>

  <div class="identity">
    <p class="person-name">JOHN DOE</p>
    <p class="person-role">POSITION</p>
  </div>

  <ul class="contact-list">
    <li class="contact-item">
      <svg class="contact-icon" viewBox="0 0 24 24"><path fill="#f2c12e" d="M6.6 10.8a15.1 15.1 0 0 0 6.6 6.6l2.2-2.2a1 1 0 0 1 1-.25 11.4 11.4 0 0 0 3.6.57 1 1 0 0 1 1 1V20a1 1 0 0 1-1 1A17 17 0 0 1 3 4a1 1 0 0 1 1-1h3.5a1 1 0 0 1 1 1c0 1.25.2 2.45.57 3.57a1 1 0 0 1-.25 1z"/></svg>
      <span>(000) 000 0000</span>
    </li>
    <li class="contact-item">
      <svg class="contact-icon" viewBox="0 0 24 24"><rect x="2" y="5" width="20" height="14" fill="#f2c12e"/><path d="M2 5l10 8 10-8" fill="none" stroke="#ffffff" stroke-width="1.6"/></svg>
      <span>email@youremail.com</span>
    </li>
    <li class="contact-item">
      <svg class="contact-icon" viewBox="0 0 24 24" fill="none" stroke="#f2c12e" stroke-width="1.8"><circle cx="12" cy="12" r="10"/><ellipse cx="12" cy="12" rx="4.5" ry="10"/><path d="M2 12h20M4 7h16M4 17h16"/></svg>
      <span>www.yourwebsite.com</span>
    </li>
  </ul>

  <div class="band-yellow"></div>
  <div class="band-black"></div>
</section>

<section class="card card-back">
  <div class="back-burst" role="img" aria-label="Dark sunburst rays radiating from the centre"></div>
  <div class="back-brand">
    <span class="back-square"></span>
    <span class="back-name">Vantro</span>
  </div>
</section>

</body>
</html>
```